sydney wedding photography business needs a business card design

we need a business card design for a sydney based wedding photography and videography business. our business name is :golden hour studio and film. our target clients are 24-35 yrs female. our style is candid, organic, natural, dynamic. we are a team of young photographers and videographers, and help brides to create memories that they will cherish for the rest of their lives. the logo will be provided. we want an elegant design that reflects our style, and also want to give a great impression to our clients that we are one of the best studios in sydney and our brand means quality and premium service.

Target Market(s)

bride to be, 24-35 years old, living in sydney and surrunding areas

Industry/Entity Type

Wedding Photography

Contact Information for Business Card

address: 57 tarrant street, glenmore nsw 2047
mobile: 0431872259
phone: (02) 9163 2408
info@tidewillowstudio.net.au
www.tidewillowstudio.net.au
facebook:tidewillowweddings
instagram:tidewillowweddings

Font styles to use
Serif
Sans Serif

Requirements
Nice to have
• maybe add my slogan"memories beyond eternity" if the layout looks good
Should not have
• no black color, not good idea for wedding biz card

```html
<!DOCTYPE html>
<html lang="en">
<head>
<meta charset="utf-8">
<title>Golden Hour Studio and Film — Business Card</title>
<link rel="stylesheet" href="https://fonts.googleapis.com/css2?family=Josefin+Sans:wght@400;600&display=swap">
<style>
  :root {
    --bg: #ece8e1;
    --gold-light: #f0c53a;
    --gold: #d9a513;
    --gold-deep: #a8760b;
    --bronze-light: #7a5120;
    --bronze: #5a3a16;
    --bronze-deep: #3f280e;
    --ink: #3d260e;
    --shadow: rgba(40, 30, 10, 0.28);
  }
  * { box-sizing: border-box; margin: 0; padding: 0; }
  html, body {
    width: 1200px; height: 950px; overflow: hidden;
    background: var(--bg);
    font-family: "Josefin Sans", sans-serif;
  }
  .stage {
    width: 1200px; height: 950px;
    display: flex; align-items: center; justify-content: center; gap: 44px;
  }
  .card {
    position: relative;
    width: 540px; height: 310px;
    border-radius: 4px; overflow: hidden;
    box-shadow: 0 14px 34px var(--shadow);
  }
  .card-front { background: linear-gradient(120deg, var(--gold-deep), var(--gold) 45%, var(--gold-light) 75%, var(--gold)); }
  .card-back  { background: radial-gradient(circle at 55% 50%, var(--gold-light), var(--gold) 55%, var(--gold-deep)); }

  .front-band { position: absolute; inset: 0; width: 100%; height: 100%; }

  .brand {
    position: absolute; left: 34px; top: 100px; width: 230px;
    color: var(--gold-light);
  }
  .brand-name {
    font-size: 25px; font-weight: 600; line-height: 1.15; letter-spacing: 0.5px;
  }
  .brand-slogan {
    margin-top: 8px;
    font-size: 10px; font-weight: 400; letter-spacing: 2.5px; text-transform: uppercase;
  }

  .contact-list {
    position: absolute; right: 26px; top: 30px;
    list-style: none; text-align: right;
    color: var(--ink); font-size: 13px; line-height: 1.45;
  }
  .contact-list li { display: flex; justify-content: flex-end; align-items: center; gap: 8px; }
  .contact-icon { width: 11px; height: 11px; flex: none; }
  .contact-square { width: 10px; height: 10px; background: var(--ink); flex: none; }
  .contact-gap { height: 8px; }

  .person {
    position: absolute; left: 250px; bottom: 30px;
    color: var(--ink);
  }
  .person-name { font-size: 19px; font-weight: 600; letter-spacing: 1px; text-transform: uppercase; }
  .person-role { font-size: 11px; letter-spacing: 1.5px; text-transform: uppercase; margin-bottom: 6px; }
  .person-address { font-size: 13px; line-height: 1.3; }

  .back-url {
    position: absolute; left: 26px; top: 22px;
    color: var(--ink); font-size: 13px; letter-spacing: 2px;
  }
  .back-mark {
    position: absolute; left: 50%; top: 50%; transform: translate(-50%, -50%);
    display: flex; align-items: center; gap: 14px;
    color: var(--ink); font-size: 20px; font-weight: 600; letter-spacing: 0.5px; white-space: nowrap;
  }
  .back-dot { width: 22px; height: 22px; border-radius: 50%; background: var(--ink); flex: none; }
</style>
</head>
<body>
<main class="stage">

  <section class="card card-front" aria-label="Card front">
    <svg class="front-band" viewBox="0 0 540 310" preserveAspectRatio="none" aria-hidden="true">
      <defs>
        <linearGradient id="bronzeGloss" x1="0" y1="0" x2="1" y2="1">
          <stop offset="0" stop-color="#7a5120"/>
          <stop offset="0.45" stop-color="#5a3a16"/>
          <stop offset="1" stop-color="#3f280e"/>
        </linearGradient>
      </defs>
      <path d="M0 0 H330 C322 120 240 200 0 268 Z" fill="url(#bronzeGloss)"/>
      <path d="M0 284 C250 214 338 128 346 0" fill="none" stroke="#3d260e" stroke-width="3"/>
    </svg>

    <div class="brand">
      <p class="brand-name">Golden Hour Studio and Film</p>
      <p class="brand-slogan">memories beyond eternity</p>
    </div>

    <ul class="contact-list">
      <li>(02) 9163 2408
        <svg class="contact-icon" viewBox="0 0 24 24" aria-hidden="true"><path fill="#3d260e" d="M6.6 10.8a15 15 0 0 0 6.6 6.6l2.2-2.2a1 1 0 0 1 1-.25 11.4 11.4 0 0 0 3.6.57 1 1 0 0 1 1 1V20a1 1 0 0 1-1 1A17 17 0 0 1 3 4a1 1 0 0 1 1-1h3.5a1 1 0 0 1 1 1c0 1.25.2 2.45.57 3.6a1 1 0 0 1-.25 1z"/></svg>
      </li>
      <li>(04) 3187 2259
        <svg class="contact-icon" viewBox="0 0 24 24" aria-hidden="true"><rect x="6" y="2" width="12" height="20" rx="2" fill="#3d260e"/><rect x="8" y="5" width="8" height="12" fill="#d9a513"/></svg>
      </li>
      <li class="contact-gap"></li>
      <li>info@tidewillowstudio.net.au</li>
      <li>tidewillowweddings <span class="contact-square"></span></li>
      <li>tidewillowweddings <span class="contact-square"></span></li>
    </ul>

    <div class="person">
      <p class="person-name">Liam Carter</p>
      <p class="person-role">Photographer</p>
      <p class="person-address">57 tarrant street<br>glenmore nsw 2047</p>
    </div>
  </section>

  <section class="card card-back" aria-label="Card back">
    <p class="back-url">www.tidewillowstudio.net.au</p>
    <div class="back-mark"><span class="back-dot"></span>Golden Hour Studio and Film</div>
  </section>

</main>
</body>
</html>
```